Business Card Design Project

Basic business card with minimal details. I just need company name, email & web address, telephone and my name.
I would like the back of the card to be grey with my logo & company name centred.

Target Market(s)

Architects
Builders
Property Developers

Industry/Entity Type

Business

Font styles to use
Sans Serif

Colors

Designer to choose colors to be used in the design.

Requirements
Must have
• Tallow Crest
Rupert Hazelby - Director
M: 0427 915203
E: rupert@tallowcrest.com.au
W: www.tallowcrest.com.au
Should not have
• No other images or pictures

```html
<!DOCTYPE html>
<html lang="en">
<head>
<meta charset="utf-8">
<title>Tallow Crest – Business Card</title>
<link rel="stylesheet" href="https://fonts.googleapis.com/css2?family=Arimo:wght@400;700&family=Michroma&display=swap">
<style>
  :root {
    --backdrop: #e4e4e2;
    --card-grey: #807f7d;
    --card-white: #ffffff;
    --name-grey: #8c8c8c;
    --accent-red: #c8202a;
    --text-white: #ffffff;
  }
  * { margin: 0; padding: 0; box-sizing: border-box; }
  html, body {
    width: 1200px;
    height: 999px;
    overflow: hidden;
    background: var(--backdrop);
    font-family: "Arimo", Arial, sans-serif;
  }
  .canvas {
    position: relative;
    width: 1200px;
    height: 999px;
    background: radial-gradient(ellipse at 50% 50%, #f7f7f6 0%, var(--backdrop) 70%);
  }
  .card {
    position: absolute;
    left: 257px;
    width: 688px;
  }
  .card-back {
    top: 79px;
    height: 392px;
    background: var(--card-grey);
    display: flex;
    align-items: center;
    justify-content: center;
  }
  .brand-name {
    font-family: "Michroma", "Arial", sans-serif;
    font-size: 40px;
    letter-spacing: 2px;
    color: var(--text-white);
    text-transform: uppercase;
    margin-top: -12px;
  }
  .card-front {
    top: 521px;
    height: 396px;
    background: var(--card-grey);
  }
  .identity {
    height: 140px;
    background: var(--card-white);
    padding: 40px 0 0 29px;
  }
  .person-name {
    font-weight: 700;
    font-size: 28px;
    color: var(--name-grey);
    text-transform: uppercase;
    line-height: 32px;
  }
  .person-role {
    font-size: 21px;
    color: var(--name-grey);
    line-height: 26px;
  }
  .contacts {
    list-style: none;
    padding: 34px 0 0 29px;
  }
  .contact {
    display: flex;
    align-items: center;
    height: 30px;
    margin-bottom: 39px;
    color: var(--text-white);
    font-size: 23px;
  }
  .contact-icon {
    width: 34px;
    height: 30px;
    margin-right: 16px;
    flex: none;
  }
</style>
</head>
<body>
<div class="canvas">
  <section class="card card-back">
    <div class="brand-name">Tallow Crest</div>
  </section>

  <section class="card card-front">
    <header class="identity">
      <div class="person-name">Rupert Hazelby</div>
      <div class="person-role">Director</div>
    </header>
    <ul class="contacts">
      <li class="contact">
        <svg class="contact-icon" viewBox="0 0 34 30" aria-hidden="true">
          <rect x="2" y="1" width="15" height="27" rx="2" fill="none" stroke="var(--accent-red)" stroke-width="1.4"/>
          <rect x="4.5" y="5" width="10" height="16" fill="none" stroke="var(--accent-red)" stroke-width="1"/>
          <circle cx="9.5" cy="24.5" r="1.3" fill="none" stroke="var(--accent-red)" stroke-width="1"/>
        </svg>
        <span>0427 915203</span>
      </li>
      <li class="contact">
        <svg class="contact-icon" viewBox="0 0 34 30" aria-hidden="true">
          <rect x="1" y="8" width="28" height="16" fill="none" stroke="var(--accent-red)" stroke-width="1.4"/>
          <path d="M1 8 L15 18 L29 8 M1 24 L11 15 M29 24 L19 15" fill="none" stroke="var(--accent-red)" stroke-width="1.2"/>
        </svg>
        <span>rupert@tallowcrest.com.au</span>
      </li>
      <li class="contact">
        <svg class="contact-icon" viewBox="0 0 34 30" aria-hidden="true">
          <text x="0" y="14" font-family="Arimo, Arial, sans-serif" font-size="11" fill="var(--accent-red)">www</text>
          <path d="M24 10 L24 24 L27 21 L29.5 26 L31 25.3 L28.6 20.5 L32 20 Z" fill="none" stroke="var(--accent-red)" stroke-width="1.1" stroke-linejoin="round"/>
        </svg>
        <span>www.tallowcrest.com.au</span>
      </li>
    </ul>
  </section>
</div>
</body>
</html>
```